Honey Company from Florida Needs Sweet and Buzz-worthy Site

Website Requests:
-Deluxe 5-Page Website with SSL-Secure Online Store (Shopify)
-High-end imagery to appeal to a discerning consumer
-Detailed verbiage with strong SEO and easy readability
-Design principles: simple, chic, luxe, earthy
Pages:
1. Home {Local, Raw American Honey from Florida}
2. The Hive
> About Us
>Meet the Beekeepers
3. Buy Honey
> Shopify retail store
4. The Buzz {News, Recipes & More}
> Blog
5. Contact Us {We're Buzzin' to Meet You}
> Store Hours
> Phone Number
> Address
> Quick Contact Form
Attachments: Web design notes, Logo, Color Codes, Inspiration Photos
Target Market(s)
High-end honey consumer in the U.S.
Industry/Entity Type
Upscale honey enthusiasts; direct to consumer sales.
Coding
Coded - Design and coding required
Number of Pages Required
5+ page
Requirements
Must have
- Upscale look and feel, easy usability for quick sales.

```html
<!DOCTYPE html>
<html lang="en">
<head>
<meta charset="utf-8">
<title>Golden Comb Honey Co.</title>
<link rel="stylesheet" href="https://fonts.googleapis.com/css2?family=Roboto:wght@500;700;900&family=Lato:wght@400;700&display=swap">
<style>
:root{
  --honey:#f5c93a;
  --ink:#1c1c1c;
  --text:#444;
  --muted:#666;
  --topbar:#1b1a1f;
  --footer:#f1f1f4;
  --line:#d8d8d8;
}
*{box-sizing:border-box;margin:0;padding:0}
html,body{width:1200px;height:4040px;overflow:hidden}
body{position:relative;background:#fff;font-family:"Lato",sans-serif;color:var(--text)}
.abs{position:absolute}
.btn{position:absolute;display:flex;align-items:center;justify-content:center;background:var(--honey);color:var(--ink);border-radius:22px;font-family:"Roboto",sans-serif;font-weight:500;text-transform:uppercase;font-size:15px}
.heading{font-family:"Roboto",sans-serif;font-weight:900;color:var(--ink);text-transform:uppercase;letter-spacing:.5px}
.photo{position:absolute}
.topbar{top:0;left:0;width:1200px;height:42px;background:var(--topbar);color:#fff;font-size:13px;font-weight:700;display:flex;align-items:center;justify-content:center}
.header{top:42px;left:0;width:1200px;height:101px;background:#fff}
.brand{top:0;left:126px;width:158px;height:158px;border-radius:50%;background:#fff;border:3px solid #f5e7b8;z-index:3;display:flex;align-items:center;justify-content:center;text-align:center;font-family:"Roboto",sans-serif;font-weight:900;font-size:22px;line-height:24px;color:var(--ink)}
.search{top:54px;left:460px;width:290px;height:42px;border:1px solid var(--line);font-size:13px;color:var(--muted);padding:13px 14px}
.search-btn{top:54px;left:750px;width:44px;height:42px;background:var(--honey);display:flex;align-items:center;justify-content:center}
.account{top:64px;left:816px;font-size:14px;color:#3a3a4a}
.nav{top:110px;left:424px;width:664px;display:flex;justify-content:space-between;font-family:"Roboto",sans-serif;font-weight:500;font-size:15px;color:var(--ink)}
.hero{top:143px;left:0;width:1200px;height:632px;background:linear-gradient(180deg,#3d3d3f 0%,#555557 60%,#6a6a6c 100%)}
.hero-photo{top:160px;left:620px;width:470px;height:570px;background:radial-gradient(ellipse at 50% 55%,#e9dcc0 0%,#c9a36a 45%,rgba(90,90,92,0) 75%)}
.hero-title{top:352px;left:116px;font-size:47px;line-height:51px;color:#fff;font-family:"Roboto",sans-serif;font-weight:700;text-transform:uppercase}
.dots{top:730px;left:560px;display:flex;gap:12px}
.dots span{width:10px;height:10px;border-radius:50%;background:#bbb}
.dots span.on{background:#fff}
.body-copy{font-size:14.5px;line-height:28px;color:var(--text)}
.sub{font-family:"Lato",sans-serif;font-weight:700;color:var(--ink)}
.product{position:absolute;width:230px}
.product .shot{height:230px;width:170px;margin-left:20px;border-radius:10px}
.product .name{margin-top:34px;font-size:16px;color:#333}
.product .price{margin-top:8px;font-family:"Roboto",sans-serif;font-weight:500;font-size:18px;color:var(--ink)}
.product .btn{position:relative;width:127px;height:40px;margin-top:16px;font-size:14px}
.jar{background:linear-gradient(180deg,#6b3f1d,#a8621c 50%,#5b3216)}
.box{background:linear-gradient(90deg,#8a5a34,#b98658 50%,#7a4c2a)}
.squeeze{background:linear-gradient(180deg,#c5c5c5 0 12%,#c68310 12%,#e8a820 60%,#b87209)}
.bullets li{list-style:none;position:relative;padding-left:24px;margin-bottom:10px}
.bullets li::before{content:"";position:absolute;left:2px;top:8px;width:11px;height:11px;border:2px solid #333;border-radius:50%;background:radial-gradient(#333 0 2px,transparent 3px)}
.feed{position:absolute;top:3457px;width:231px;height:235px}
.footer{top:3692px;left:0;width:1200px;height:348px;background:var(--footer)}
.fh{font-size:15px;color:var(--ink);text-transform:uppercase}
.fl{font-size:13px;line-height:26px;color:#555}
</style>
</head>
<body>

<div class="abs topbar">Free shipping on all orders over $100! Click here to learn more!</div>
<div class="abs header"></div>
<div class="abs brand">GOLDEN<br>COMB<br>HONEY CO.</div>
<div class="abs search">Search Store..</div>
<div class="abs search-btn"><svg width="22" height="22" viewBox="0 0 22 22"><circle cx="9" cy="9" r="7" fill="none" stroke="#222" stroke-width="2"/><line x1="14" y1="14" x2="20" y2="20" stroke="#222" stroke-width="2"/></svg></div>
<div class="abs account">Sign in &nbsp;|&nbsp; Create account &nbsp;|&nbsp; Checkout &nbsp;<svg width="18" height="15" viewBox="0 0 18 15"><path d="M1 2h3l2 8h9l2-6H5" fill="none" stroke="#333" stroke-width="1.5"/><circle cx="7" cy="13" r="1.4" fill="#333"/><circle cx="14" cy="13" r="1.4" fill="#333"/></svg></div>
<nav class="abs nav"><span>Home</span><span>The Hive ⌄</span><span>Buy Honey</span><span>The Buzz ⌄</span><span>Contact Us</span></nav>

<section class="abs hero"></section>
<div class="photo hero-photo" role="img" aria-label="Honey jar with a patterned lid beside an open gift box and scattered bees"></div>
<h1 class="abs hero-title">Straight from our<br>beloved hives to<br>your lovely home</h1>
<div class="btn" style="top:529px;left:114px;width:134px;height:40px">Shop Now</div>
<svg class="abs" style="top:460px;left:74px" width="24" height="44" viewBox="0 0 24 44"><polyline points="22,2 2,22 22,42" fill="none" stroke="#fff" stroke-width="2"/></svg>
<svg class="abs" style="top:460px;left:1100px" width="24" height="44" viewBox="0 0 24 44"><polyline points="2,2 22,22 2,42" fill="none" stroke="#fff" stroke-width="2"/></svg>
<div class="abs dots"><span></span><span class="on"></span><span></span><span></span></div>

<div class="photo" style="top:864px;left:111px;width:476px;height:421px;background:linear-gradient(180deg,#7a8d6a,#a9a98e 45%,#6f7a52)" role="img" aria-label="Beekeeper in a protective suit standing beside stacked hive boxes"></div>
<h2 class="abs heading" style="top:870px;left:637px;font-size:38px">About Us</h2>
<p class="abs body-copy" style="top:926px;left:637px;width:450px">100% raw, unfiltered Florida honey straight from he beehives on his six-acre property, Golden Comb Honey Farm, 4180 Orchard Lane in Lakeview. Agricultural Company specializing in the Production of 100% Raw American Honey, and the Pollination of America’s food crops. Our Honey comes straight from our beehives to your table. No filtering, heating, or any funny stuff. Just All Natural, 100% Pure Florida Honey Natural Wild Honey- flavors include Orange Blossom, Gallberry, Summer Wildflower, Winter Wildflower, and many more. Bee Pollen, Royal Jelly, and Bee venom. Bee removals are done by Walt.</p>
<div class="btn" style="top:1226px;left:637px;width:146px;height:46px">Learn More</div>

<h2 class="abs heading" style="top:1370px;left:0;width:1200px;text-align:center;font-size:38px">Featured Products</h2>
<div class="product" style="top:1443px;left:111px"><div class="shot box" role="img" aria-label="Boxed honey jar"></div><div class="name">Finibus Bonorum et Malorum</div><div class="price">$500.00</div><div class="btn">Add to cart</div></div>
<div class="product" style="top:1443px;left:367px"><div class="shot squeeze" role="img" aria-label="Wildflower honey squeeze bottle"></div><div class="name">Finibus Bonorum et Malorum</div><div class="price">$500.00</div><div class="btn">Add to cart</div></div>
<div class="product" style="top:1443px;left:621px"><div class="shot jar" role="img" aria-label="Large dark honey bottle"></div><div class="name">Finibus Bonorum et Malorum</div><div class="price">$500.00</div><div class="btn">Add to cart</div></div>
<div class="product" style="top:1443px;left:875px"><div class="shot squeeze" role="img" aria-label="Wildflower honey squeeze bottle"></div><div class="name">Finibus Bonorum et Malorum</div><div class="price">$500.00</div><div class="btn">Add to cart</div></div>

<h2 class="abs heading" style="top:1886px;left:111px;font-size:38px">Importance of Bees</h2>
<div class="abs sub" style="top:1938px;left:111px;font-size:18px">Don’t Judge a Bee by Its Stinger</div>
<ul class="abs bullets body-copy" style="top:1970px;left:111px;width:460px;font-size:14px;line-height:26px">
<li>Hyper-efficient insects do play a vital role in agriculture. Almonds, for example, are almost entirely dependent on honeybee pollination</li>
<li>Over one-third of our entire diet is dependent on pollination from the honeybee. So, for every three bites of food you eat, you can thank the honeybee for one of those three bites,” Walt says</li>
<li>They are very misunderstood among the public. We have lost a great amount of our natural forage land due to urbanization and suburban sprawl, and when people and honeybees</li>
</ul>
<div class="btn" style="top:2246px;left:111px;width:146px;height:46px">Learn More</div>
<div class="photo" style="top:1885px;left:612px;width:475px;height:421px;background:linear-gradient(180deg,#b9c9d6,#8fa676 40%,#5f7a3d)" role="img" aria-label="Beekeeper in a veil inspecting a honeycomb frame in a field"></div>

<h2 class="abs heading" style="top:2390px;left:0;width:1200px;text-align:center;font-size:38px">Best Sellers</h2>
<div class="product" style="top:2458px;left:111px"><div class="shot jar" role="img" aria-label="Large dark honey bottle"></div><div class="name">Finibus Bonorum et Malorum</div><div class="price">$500.00</div><div class="btn">Add to cart</div></div>
<div class="product" style="top:2458px;left:367px"><div class="shot box" role="img" aria-label="Boxed honey jar"></div><div class="name">Finibus Bonorum et Malorum</div><div class="price">$500.00</div><div class="btn">Add to cart</div></div>
<div class="product" style="top:2458px;left:621px"><div class="shot squeeze" role="img" aria-label="Wildflower honey squeeze bottle"></div><div class="name">Finibus Bonorum et Malorum</div><div class="price">$500.00</div><div class="btn">Add to cart</div></div>
<div class="product" style="top:2458px;left:875px"><div class="shot box" role="img" aria-label="Boxed honey jar"></div><div class="name">Finibus Bonorum et Malorum</div><div class="price">$500.00</div><div class="btn">Add to cart</div></div>

<div class="photo" style="top:2905px;left:111px;width:476px;height:420px;background:linear-gradient(180deg,#2e2420,#4a3026 50%,#3a2a22)" role="img" aria-label="Wooden shelves lined with jars of honey and framed pictures"></div>
<h2 class="abs heading" style="top:2930px;left:637px;font-size:36px;line-height:40px">The Health Benefits<br>of Honey</h2>
<div class="abs" style="top:3020px;left:635px;font-size:21px;color:var(--ink)">Real Local Honey, Really Good for You</div>
<p class="abs body-copy" style="top:3064px;left:637px;width:450px">Raw honey is loaded with antioxidants to protect your body from cell damage due to free radicals. Honey has been long known as a folk remedy to help heal burns and wounds due to its antibacterial and antifungal properties. Honey is also very well known to soothe a sore throat. Try taking a spoonful of honey and add it to hot tea if you feel like you have a cold. Honey can also help as a cough suppressant.</p>
<div class="btn" style="top:3252px;left:637px;width:146px;height:46px">Learn More</div>

<h2 class="abs heading" style="top:3398px;left:0;width:1200px;text-align:center;font-size:29px;font-weight:700">Follow Our Hive Feed</h2>
<div class="feed" style="left:0;background:linear-gradient(135deg,#d8d000,#8a6a08 60%,#3b2a06)" role="img" aria-label="Honey bottles with yellow caps"></div>
<div class="feed" style="left:242px;background:linear-gradient(180deg,#3a6a2a,#c65a18 55%,#7a2a10)" role="img" aria-label="Jar of honey with a gingham lid"></div>
<div class="feed" style="left:483px;background:linear-gradient(180deg,#3a2010,#b8720e 50%,#f0c020)" role="img" aria-label="Honey jars behind beeswax blocks"></div>
<div class="feed" style="left:726px;background:linear-gradient(180deg,#5a5040,#8a4a20 50%,#d8d8dc)" role="img" aria-label="Market table with honey jars"></div>
<div class="feed" style="left:968px;width:232px;background:linear-gradient(180deg,#7a8a60,#b0a888 50%,#6a6a4a)" role="img" aria-label="Beekeeper beside hive boxes"></div>

<footer class="abs footer"></footer>
<div class="abs fh" style="top:3744px;left:113px">Contact Us</div>
<div class="abs fl" style="top:3774px;left:113px">4180 Orchard Lane, Lakeview, FL 32000<br>(555) 014-2290</div>
<div class="abs" style="top:3846px;left:113px;display:flex;gap:12px" aria-label="Social links"><span style="width:12px;height:12px;border-radius:50%;background:#333"></span><span style="width:12px;height:12px;border-radius:50%;background:#333"></span><span style="width:12px;height:12px;border-radius:50%;background:#333"></span></div>
<div class="abs fh" style="top:3744px;left:471px">Shop</div>
<div class="abs fl" style="top:3774px;left:471px">Home<br>The Hive<br>Buy Honey<br>The Buzz<br>Contact Us</div>
<div class="abs fh" style="top:3744px;left:631px">About</div>
<div class="abs fl" style="top:3774px;left:631px">Story<br>Journal<br>FAQ<br>Terms of Usage</div>
<div class="abs fh" style="top:3744px;left:833px">Newsletter</div>
<div class="abs fl" style="top:3774px;left:833px;width:260px">Subscribe to receive updates, access to exclusive deals, and more.</div>
<div class="abs" style="top:3838px;left:833px;width:258px;height:44px;background:#fff;border:1px solid #bbb;font-size:13px;color:#555;padding:13px 14px">Enter Your Email</div>
<div class="btn" style="top:3905px;left:833px;width:136px;height:46px">Subscribe</div>
<div class="abs" style="top:3990px;left:113px;font-size:13px;color:#333">Copyright © 2021 GOLDENCOMB . All Rights Reserved.</div>
<div class="abs" style="top:3990px;left:830px;display:flex;gap:14px" aria-label="Accepted payment methods">
<span style="width:26px;height:16px;background:#d9d9e6;border-radius:2px"></span><span style="width:26px;height:16px;background:#d9d9e6;border-radius:2px"></span><span style="width:26px;height:16px;background:#d9d9e6;border-radius:2px"></span><span style="width:26px;height:16px;background:#d9d9e6;border-radius:2px"></span><span style="width:26px;height:16px;background:#d9d9e6;border-radius:2px"></span><span style="width:26px;height:16px;background:#d9d9e6;border-radius:2px"></span>
</div>

</body>
</html>
```